Soap Company Looking To Design New Soap Scent Boxes

we are looking to create a soap box similar to vel korrin. we would like the circle cut out on the top right corner of the box. we are looking for a design that will allow us to use different color base banners for different soap scents (like vel. korrin). we want the soap name scents to be large and readable on the bottom banner (like vel.korrin). we have included our brand figure (logo) and some previous older soap box designs that we were making before the brand figure. the box dims are attached.

```html
<!DOCTYPE html>
<html lang="en">
<head>
<meta charset="utf-8">
<title>Hollowmere — Natural Soap Boxes</title>
<link rel="stylesheet" href="https://fonts.googleapis.com/css2?family=Montserrat:wght@500;700;800;900&display=swap">
<style>
  :root {
    --kraft: #e7d8bf;
    --kraft-dark: #dccbae;
    --ink: #3a2418;
    --white: #ffffff;
    --placeholder-light: #d3c3a6;
    --placeholder-dark: #bfac8b;
    --nag-champa-band: #8b4b2f;   --nag-champa-dot: #a2624b;
    --plumeria-band: #bf1a6c;     --plumeria-dot: #d01b80;
    --pomegranate-band: #c11f26;  --pomegranate-dot: #d2222c;
    --rasp-rush-band: #d4166f;    --rasp-rush-dot: #e9198b;
    --rasp-vanilla-band: #e8434a; --rasp-vanilla-dot: #f15b5b;
    --sandalwood-band: #791818;   --sandalwood-dot: #7d1b1b;
    --tangerine-band: #e5561b;    --tangerine-dot: #f0661f;
    --passion-band: #8e3a72;      --passion-dot: #9c4b87;
    --wildflower-band: #cb2026;   --wildflower-dot: #d52b2b;
  }
  * { margin: 0; padding: 0; box-sizing: border-box; }
  html, body { width: 1200px; height: 1195px; overflow: hidden; background: var(--white); }
  .box-sheet {
    width: 1200px; height: 1195px;
    display: grid;
    grid-template-columns: repeat(3, 386px);
    grid-template-rows: repeat(3, 386px);
    column-gap: 21px; row-gap: 18.5px;
    font-family: "Montserrat", Arial, sans-serif;
  }
  .soap-box {
    position: relative; overflow: hidden;
    background: linear-gradient(160deg, var(--kraft) 0%, var(--kraft-dark) 100%);
  }
  .box-art { position: absolute; inset: 0; width: 386px; height: 386px; }
  .band-shape { fill: var(--band); }
  .window-ring { fill: var(--white); }
  .window-fill { fill: var(--dot); }
  .brand-figure {
    position: absolute; left: 78px; top: 10px; width: 132px; height: 152px;
    border-radius: 50%;
    border: 6px solid var(--white);
    background: linear-gradient(180deg, var(--placeholder-light) 0%, var(--placeholder-dark) 100%);
  }
  .brand-name {
    position: absolute; left: 30px; top: 160px;
    font-size: 42px; font-weight: 900; color: var(--ink);
    letter-spacing: -1px; line-height: 1;
  }
  .box-label {
    position: absolute; left: 0; right: 0; top: 275px;
    text-align: center; color: var(--white);
  }
  .label-kicker { font-size: 17px; font-weight: 500; letter-spacing: 0.5px; }
  .scent-name {
    height: 40px; line-height: 40px; margin-top: 2px;
    font-size: 32px; font-weight: 800;
    white-space: nowrap; letter-spacing: 0.3px;
  }
  .scent-name.is-long { font-size: 25px; }
  .scent-name.is-mid { font-size: 28px; }
  .label-fine {
    font-size: 10.5px; font-weight: 700; margin-top: 6px;
    display: flex; justify-content: center; align-items: center; gap: 5px;
  }
  .fine-tag { background: var(--white); color: var(--band); padding: 1px 4px; }
  .nag-champa   { --band: var(--nag-champa-band);   --dot: var(--nag-champa-dot); }
  .plumeria     { --band: var(--plumeria-band);     --dot: var(--plumeria-dot); }
  .pomegranate  { --band: var(--pomegranate-band);  --dot: var(--pomegranate-dot); }
  .rasp-rush    { --band: var(--rasp-rush-band);    --dot: var(--rasp-rush-dot); }
  .rasp-vanilla { --band: var(--rasp-vanilla-band); --dot: var(--rasp-vanilla-dot); }
  .sandalwood   { --band: var(--sandalwood-band);   --dot: var(--sandalwood-dot); }
  .tangerine    { --band: var(--tangerine-band);    --dot: var(--tangerine-dot); }
  .passion      { --band: var(--passion-band);      --dot: var(--passion-dot); }
  .wildflower   { --band: var(--wildflower-band);   --dot: var(--wildflower-dot); }
</style>
</head>
<body>
<main class="box-sheet">

  <section class="soap-box nag-champa">
    <svg class="box-art" viewBox="0 0 386 386"><path class="band-shape" d="M0 232 C120 228 260 212 386 178 L386 386 L0 386 Z"/><circle class="window-ring" cx="282" cy="92" r="74"/><circle class="window-fill" cx="282" cy="92" r="64"/></svg>
    <div class="brand-figure" role="img" aria-label="Brand figure illustration"></div>
    <div class="brand-name">Hollowmere</div>
    <div class="box-label"><div class="label-kicker">NATURAL SOAP</div><div class="scent-name">NAG CHAMPA</div><div class="label-fine">COLD PRESSED <span class="fine-tag">ARTISAN SOAP</span> Net Wt. 5Oz / 140g</div></div>
  </section>

  <section class="soap-box plumeria">
    <svg class="box-art" viewBox="0 0 386 386"><path class="band-shape" d="M0 232 C120 228 260 212 386 178 L386 386 L0 386 Z"/><circle class="window-ring" cx="282" cy="92" r="74"/><circle class="window-fill" cx="282" cy="92" r="64"/></svg>
    <div class="brand-figure" role="img" aria-label="Brand figure illustration"></div>
    <div class="brand-name">Hollowmere</div>
    <div class="box-label"><div class="label-kicker">NATURAL SOAP</div><div class="scent-name">PLUMERIA</div><div class="label-fine">COLD PRESSED <span class="fine-tag">ARTISAN SOAP</span> Net Wt. 5Oz / 140g</div></div>
  </section>

  <section class="soap-box pomegranate">
    <svg class="box-art" viewBox="0 0 386 386"><path class="band-shape" d="M0 232 C120 228 260 212 386 178 L386 386 L0 386 Z"/><circle class="window-ring" cx="282" cy="92" r="74"/><circle class="window-fill" cx="282" cy="92" r="64"/></svg>
    <div class="brand-figure" role="img" aria-label="Brand figure illustration"></div>
    <div class="brand-name">Hollowmere</div>
    <div class="box-label"><div class="label-kicker">NATURAL SOAP</div><div class="scent-name is-long">POMEGRANATE CHERRY</div><div class="label-fine">COLD PRESSED <span class="fine-tag">ARTISAN SOAP</span> Net Wt. 5Oz / 140g</div></div>
  </section>

  <section class="soap-box rasp-rush">
    <svg class="box-art" viewBox="0 0 386 386"><path class="band-shape" d="M0 232 C120 228 260 212 386 178 L386 386 L0 386 Z"/><circle class="window-ring" cx="282" cy="92" r="74"/><circle class="window-fill" cx="282" cy="92" r="64"/></svg>
    <div class="brand-figure" role="img" aria-label="Brand figure illustration"></div>
    <div class="brand-name">Hollowmere</div>
    <div class="box-label"><div class="label-kicker">NATURAL SOAP</div><div class="scent-name is-mid">RASPBERRY RUSH</div><div class="label-fine">COLD PRESSED <span class="fine-tag">ARTISAN SOAP</span> Net Wt. 5Oz / 140g</div></div>
  </section>

  <section class="soap-box rasp-vanilla">
    <svg class="box-art" viewBox="0 0 386 386"><path class="band-shape" d="M0 232 C120 228 260 212 386 178 L386 386 L0 386 Z"/><circle class="window-ring" cx="282" cy="92" r="74"/><circle class="window-fill" cx="282" cy="92" r="64"/></svg>
    <div class="brand-figure" role="img" aria-label="Brand figure illustration"></div>
    <div class="brand-name">Hollowmere</div>
    <div class="box-label"><div class="label-kicker">NATURAL SOAP</div><div class="scent-name is-long">RASPBERRY VANILLA</div><div class="label-fine">COLD PRESSED <span class="fine-tag">ARTISAN SOAP</span> Net Wt. 5Oz / 140g</div></div>
  </section>

  <section class="soap-box sandalwood">
    <svg class="box-art" viewBox="0 0 386 386"><path class="band-shape" d="M0 232 C120 228 260 212 386 178 L386 386 L0 386 Z"/><circle class="window-ring" cx="282" cy="92" r="74"/><circle class="window-fill" cx="282" cy="92" r="64"/></svg>
    <div class="brand-figure" role="img" aria-label="Brand figure illustration"></div>
    <div class="brand-name">Hollowmere</div>
    <div class="box-label"><div class="label-kicker">NATURAL SOAP</div><div class="scent-name is-mid">SANDALWOOD ROSE</div><div class="label-fine">COLD PRESSED <span class="fine-tag">ARTISAN SOAP</span> Net Wt. 5Oz / 140g</div></div>
  </section>

  <section class="soap-box tangerine">
    <svg class="box-art" viewBox="0 0 386 386"><path class="band-shape" d="M0 232 C120 228 260 212 386 178 L386 386 L0 386 Z"/><circle class="window-ring" cx="282" cy="92" r="74"/><circle class="window-fill" cx="282" cy="92" r="64"/></svg>
    <div class="brand-figure" role="img" aria-label="Brand figure illustration"></div>
    <div class="brand-name">Hollowmere</div>
    <div class="box-label"><div class="label-kicker">NATURAL SOAP</div><div class="scent-name is-long">TANGERINE GRAPEFRUIT</div><div class="label-fine">COLD PRESSED <span class="fine-tag">ARTISAN SOAP</span> Net Wt. 5Oz / 140g</div></div>
  </section>

  <section class="soap-box passion">
    <svg class="box-art" viewBox="0 0 386 386"><path class="band-shape" d="M0 232 C120 228 260 212 386 178 L386 386 L0 386 Z"/><circle class="window-ring" cx="282" cy="92" r="74"/><circle class="window-fill" cx="282" cy="92" r="64"/></svg>
    <div class="brand-figure" role="img" aria-label="Brand figure illustration"></div>
    <div class="brand-name">Hollowmere</div>
    <div class="box-label"><div class="label-kicker">NATURAL SOAP</div><div class="scent-name">WILD PASSION</div><div class="label-fine">COLD PRESSED <span class="fine-tag">ARTISAN SOAP</span> Net Wt. 5Oz / 140g</div></div>
  </section>

  <section class="soap-box wildflower">
    <svg class="box-art" viewBox="0 0 386 386"><path class="band-shape" d="M0 232 C120 228 260 212 386 178 L386 386 L0 386 Z"/><circle class="window-ring" cx="282" cy="92" r="74"/><circle class="window-fill" cx="282" cy="92" r="64"/></svg>
    <div class="brand-figure" role="img" aria-label="Brand figure illustration"></div>
    <div class="brand-name">Hollowmere</div>
    <div class="box-label"><div class="label-kicker">NATURAL SOAP</div><div class="scent-name">WILD FLOWERS</div><div class="label-fine">COLD PRESSED <span class="fine-tag">ARTISAN SOAP</span> Net Wt. 5Oz / 140g</div></div>
  </section>

</main>
</body>
</html>
```